Website for my photography business

I need a website for my photography business, Bram Kellet Photography. I need a website that has a landing page with a cover photo of each kind of photography I do. For example, Nature, Weddings, Portraits and Architecture. I want it so that when someone comes onto my website they have to choose which kind of photography page they want to visit. So if they click on the wedding photo it will open to a page with my wedding portfolio images and a contact me button. If they choose nature photography I want them to be redirected to an e-commerce section where they can purchase prints. Architecture and Portraits should open up to their respective portfolios with about me and contact info. I like this kind of format because I want people who come to my website for a specific type of photography to be able to be directed there easily without having to look at a mix of other kinds of photography. I will provide a few files to use as placeholders. I have already purchased the bramkelletphotography.example domain name. A Wix website would be great because I am most familiar with it but I am open to anything.

Industry/Entity Type

Photographer

Number of Pages Required

5+ page

Requirements
Must have
• Landing Page and e-commerce

```html
<!DOCTYPE html>
<html lang="en">
<head>
<meta charset="utf-8">
<title>Bram Kellet Photography – Nature</title>
<link rel="stylesheet" href="https://fonts.googleapis.com/css2?family=Poppins:wght@400;500;600&family=Great+Vibes&display=swap">
<style>
:root{
  --purple:#3d3466;
  --purple-deep:#352d5c;
  --teal:#1d4e6b;
  --ink:#2b2b2b;
  --muted:#555;
  --topbar:#f4f4f4;
  --card:#f6f6f6;
  --card-line:#e2e2e2;
  --white:#fff;
}
*{box-sizing:border-box;margin:0;padding:0}
html,body{width:1200px;height:2245px;overflow:hidden}
body{position:relative;font-family:'Poppins',sans-serif;color:var(--ink);background:var(--white)}
.topbar{position:absolute;top:0;left:0;width:1200px;height:32px;background:var(--topbar);border-bottom:1px solid #dcdcdc;font-size:12px;color:var(--muted);text-align:center;line-height:31px}
.header{position:absolute;top:32px;left:0;width:1200px;height:100px}
.brand{position:absolute;left:112px;top:34px;display:flex;align-items:center;gap:10px;font-size:20px;font-weight:500;color:var(--purple)}
.brand-dot{width:22px;height:22px;border-radius:50%;background:var(--purple)}
.social-top{position:absolute;left:669px;top:33px;display:flex;gap:4px}
.social-top span{width:37px;height:37px;border:2px solid #222;border-radius:50%}
.call{position:absolute;left:871px;top:30px;width:217px;height:43px;border-radius:22px;background:var(--teal);color:var(--white);font-weight:600;font-size:16.5px;text-align:center;line-height:43px}
.nav{position:absolute;top:132px;left:0;width:1200px;height:40px;background:var(--purple);display:flex;justify-content:center;padding-left:4px}
.nav a{color:var(--white);text-decoration:none;font-size:15px;font-weight:500;line-height:40px;padding:0 17px}
.nav a.active{background:var(--teal)}
.hero{position:absolute;top:172px;left:0;width:1200px;height:399px;background:
  radial-gradient(ellipse 200px 260px at 600px 230px,#c06a2c 0%,#9a5328 45%,transparent 75%),
  radial-gradient(ellipse 380px 140px at 1000px 360px,#f1f3f6 0%,#dfe3ea 60%,transparent 100%),
  radial-gradient(ellipse 300px 120px at 300px 390px,#e8ebf0 0%,transparent 100%),
  linear-gradient(160deg,#1f2a22 0%,#34402f 35%,#2a3326 65%,#a6adb4 100%)}
.hero-panel{position:absolute;left:346px;top:114px;width:508px;height:178px;background:rgba(55,47,96,.78);text-align:center;color:var(--white)}
.hero-panel h1{font-family:'Great Vibes',cursive;font-weight:400;font-size:48px;margin-top:14px;line-height:1.1}
.hero-panel p{font-size:17px;font-weight:500;line-height:27px;margin-top:10px}
.section-title{position:absolute;top:648px;left:0;width:1200px;text-align:center;font-family:'Great Vibes',cursive;font-size:42px;color:var(--purple);font-weight:400}
.grid{position:absolute;top:748px;left:112px;display:grid;grid-template-columns:repeat(4,230px);column-gap:19px;row-gap:36px}
.card{width:230px;height:307px;background:var(--card);border:1px solid var(--card-line)}
.card-photo{height:226px}
.card-name{font-size:17px;padding:16px 0 0 16px;line-height:22px}
.card-price{font-size:15px;font-weight:600;color:var(--purple);padding-left:16px;line-height:22px;margin-top:2px}
.footer{position:absolute;top:1853px;left:0;width:1200px;height:392px;background:var(--purple);color:var(--white)}
.fcol{position:absolute;top:96px}
.fcol h3{font-size:16.5px;font-weight:500;text-transform:uppercase;margin-bottom:16px}
.fcol li{list-style:none;font-size:13px;line-height:26.4px}
.contact li{display:flex;align-items:flex-start;gap:10px;line-height:16px;margin-bottom:13px}
.contact svg{flex:none;margin-top:1px}
.contact u{text-underline-offset:2px}
.email{width:265px;height:37px;border-radius:19px;background:var(--white);color:#666;font-size:13px;line-height:37px;padding-left:17px;margin-top:30px}
.submit{width:153px;height:37px;border-radius:19px;background:var(--teal);font-weight:600;font-size:15px;text-align:center;line-height:37px;margin-top:13px}
.social-foot{display:flex;gap:6px;margin:25px 0 0 18px}
.social-foot span{width:37px;height:37px;border-radius:50%;background:var(--white)}
.rule{position:absolute;top:323px;left:112px;width:976px;height:1px;background:rgba(255,255,255,.15)}
.copy{position:absolute;top:344px;left:0;width:1200px;text-align:center;font-size:13.5px}
</style>
</head>
<body>
<div class="topbar">Lorem ipsum dolor sit amet, consectetur adipiscing elit,</div>

<header class="header">
  <div class="brand"><span class="brand-dot"></span>Bram Kellet Photography</div>
  <div class="social-top" aria-label="Social links"><span></span><span></span><span></span><span></span></div>
  <div class="call">Call Us:&nbsp; 123-456-789</div>
</header>

<nav class="nav">
  <a href="#">Home</a><a href="#">About Me</a><a href="#" class="active">Nature</a><a href="#">Weddings</a><a href="#">Potraits</a><a href="#">Architecture</a><a href="#">Shop</a><a href="#">portfolio</a><a href="#">News</a><a href="#">Contact Us</a>
</nav>

<section class="hero" role="img" aria-label="Red fox sitting on snowy rocks among pine branches">
  <div class="hero-panel">
    <h1>Nature</h1>
    <p>Lorem ipsum dolor sit amet, consectetur adipiscing<br>elit, sed do eiusmod tempor incididunt</p>
  </div>
</section>

<h2 class="section-title">Nature Portfolio</h2>

<main class="grid">
  <div class="card"><div class="card-photo" role="img" aria-label="Turquoise waterfall cascading through jungle" style="background:linear-gradient(180deg,#3c6b35,#8fb0a8 55%,#3fa3a8)"></div><div class="card-name">Product Name</div><div class="card-price">$15.36</div></div>
  <div class="card"><div class="card-photo" role="img" aria-label="Kingfisher diving toward water" style="background:radial-gradient(circle at 50% 50%,#b9783a,#56642a 50%,#2d3a18)"></div><div class="card-name">Product Name</div><div class="card-price">$15.36</div></div>
  <div class="card"><div class="card-photo" role="img" aria-label="Two tigers walking on a dirt path" style="background:linear-gradient(180deg,#7a8068,#a9916f 45%,#8c7d6d)"></div><div class="card-name">Product Name</div><div class="card-price">$15.36</div></div>
  <div class="card"><div class="card-photo" role="img" aria-label="Pack of grey wolves on rocks" style="background:linear-gradient(180deg,#8d9286,#6b6e66 50%,#4e5148)"></div><div class="card-name">Product Name</div><div class="card-price">$15.36</div></div>

  <div class="card"><div class="card-photo" role="img" aria-label="Boat in a lagoon beneath green cliffs" style="background:linear-gradient(180deg,#2f6fc0,#2f5a2c 40%,#3a7a3a 60%,#2ea6b6)"></div><div class="card-name">Product Name</div><div class="card-price">$15.36</div></div>
  <div class="card"><div class="card-photo" role="img" aria-label="Deer grazing in a sunlit autumn meadow" style="background:radial-gradient(circle at 55% 45%,#f0dd8a,#b89a3a 50%,#6d4b1e)"></div><div class="card-name">Product Name</div><div class="card-price">$15.36</div></div>
  <div class="card"><div class="card-photo" role="img" aria-label="Pink flower meadow under stormy sky" style="background:linear-gradient(180deg,#2e3a55,#c9ccd0 35%,#5c7a44 60%,#c84c9a)"></div><div class="card-name">Product Name</div><div class="card-price">$15.36</div></div>
  <div class="card"><div class="card-photo" role="img" aria-label="Puppy and kitten sitting on grass" style="background:radial-gradient(circle at 60% 40%,#e6c89a,#3a3a22 60%,#12140c)"></div><div class="card-name">Product Name</div><div class="card-price">$15.36</div></div>

  <div class="card"><div class="card-photo" role="img" aria-label="Two bee-eater birds perched on a branch" style="background:radial-gradient(circle at 40% 40%,#b8d46a,#5f8f2a 55%,#2f4d18)"></div><div class="card-name">Product Name</div><div class="card-price">$15.36</div></div>
  <div class="card"><div class="card-photo" role="img" aria-label="Autumn trees beside a river" style="background:linear-gradient(135deg,#c48a25,#6b4a1c 45%,#5a8a2a 65%,#1f3f8a)"></div><div class="card-name">Product Name</div><div class="card-price">$15.36</div></div>
  <div class="card"><div class="card-photo" role="img" aria-label="Three giraffes on a savanna" style="background:linear-gradient(180deg,#b6c0cc,#c4ccd4 50%,#8a7650 80%,#5f6a4a)"></div><div class="card-name">Product Name</div><div class="card-price">$15.36</div></div>
  <div class="card"><div class="card-photo" role="img" aria-label="Rocky coastline under a lightning storm" style="background:linear-gradient(180deg,#1f3d7a,#6a8fc0 40%,#b08040 65%,#1a7a8a)"></div><div class="card-name">Product Name</div><div class="card-price">$15.36</div></div>
</main>

<footer class="footer">
  <div class="fcol" style="left:112px">
    <h3>Contact Info</h3>
    <ul class="contact">
      <li><svg width="14" height="14" viewBox="0 0 14 14"><path d="M1 5c0-2 2-3 6-3s6 1 6 3v1H10V4.5H4V6H1z M3 7h8l1 5H2z" fill="#fff"/></svg>(888) 888-8888</li>
      <li><svg width="14" height="14" viewBox="0 0 14 14"><rect x="3" y="1" width="8" height="4" fill="#fff"/><rect x="1" y="5" width="12" height="5" fill="#fff"/><rect x="3" y="9" width="8" height="4" fill="#fff" stroke="#3d3466"/></svg>(888) 888-888</li>
      <li><svg width="14" height="14" viewBox="0 0 14 14"><rect x="1" y="3" width="12" height="8" fill="#fff"/><path d="M1 3l6 5 6-5" fill="none" stroke="#3d3466"/></svg><u>hello@bramkellet.example</u></li>
      <li><svg width="14" height="14" viewBox="0 0 14 14"><path d="M7 1a4 4 0 0 1 4 4c0 3-4 8-4 8S3 8 3 5a4 4 0 0 1 4-4z" fill="#fff"/><circle cx="7" cy="5" r="1.5" fill="#3d3466"/></svg>#2868 Lorem ipsum dolor<br>sit amet, consectetur</li>
    </ul>
  </div>
  <div class="fcol" style="left:372px">
    <h3>Quick Links</h3>
    <ul><li>Home</li><li>About</li><li>Professional Gamer</li><li>Reviews</li><li>Gallery</li></ul>
  </div>
  <div class="fcol" style="left:600px">
    <h3>Information</h3>
    <ul><li>Terms &amp; Conditions</li><li>Privacy Policy</li><li>Disclaimer</li><li>Site Map</li><li>Contact Us</li></ul>
  </div>
  <div class="fcol" style="left:820px">
    <h3>Newsletter Subscription</h3>
    <div class="email" style="margin-top:14px">Enter your email</div>
    <div class="submit">SUBMIT</div>
    <div class="social-foot" aria-label="Social links"><span></span><span></span><span></span><span></span></div>
  </div>
  <div class="rule"></div>
  <div class="copy">© Copyright 2020 Bram Kellet Photography, All Rights Reserved</div>
</footer>
</body>
</html>
```